Design concept Visual UI of future mobile app - healthcare

Hi,
I'm looking for a top designer, innovative with strong experience in user interface

The app will be connected to a future health website related to depression and addiction by helping the user to track the moods, tired, anxiety using this mobile app.

I attached the deck of the overall project but I can send you a specific presentation for the app only

thanks

Target Market(s)

Switzerland, UK, Germany and France

Industry/Entity Type

Mental Health

Logo Text

Health, hope

Font styles to use
Sans Serif

Colors
cee9f5
33a6d7
0692cd
0255a3
3276b5
85abd2

Requirements
Must have
• keep it simple, easy to navigate
• The user should be able to track the moods on a daily basis,
• sleep time, and rate how the feel on the day
• To be able to get information from the sync deck of vexlo
Nice to have
• to be able share this app with a friend

```html
<!DOCTYPE html>
<html lang="en">
<head>
<meta charset="utf-8">
<title>Steady Mind – App Screens</title>
<link rel="stylesheet" href="https://fonts.googleapis.com/css2?family=Roboto:wght@300;400;500;700&display=swap">
<style>
  :root {
    --page: #f2f2f2;
    --sky-top: #2f8fd6;
    --sky-mid: #4aa6e2;
    --sky-low: #8cc6ec;
    --ink: #ffffff;
    --bar-dark: #111111;
    --bar-light: #ffffff;
    --btn: rgba(120, 185, 230, 0.75);
    --mood-1: #e8402a;
    --mood-2: #f06a24;
    --mood-3: #ee8a2c;
    --mood-4: #dcaa2e;
    --mood-5: #a38b33;
    --mood-6: #8f9637;
    --mood-7: #899b3b;
    --mood-8: #7c8a39;
    --mood-9: #7a7b3b;
    --mood-10: #666650;
    --time-box: #2c6fb2;
  }
  * { box-sizing: border-box; margin: 0; padding: 0; }
  html, body { width: 1200px; height: 800px; overflow: hidden; }
  body { background: var(--page); font-family: "Roboto", Arial, sans-serif; color: var(--ink); position: relative; }

  .screen {
    position: absolute; top: 228px; width: 188px; height: 334px; overflow: hidden;
    background: linear-gradient(180deg, var(--sky-top) 0%, var(--sky-mid) 55%, var(--sky-low) 100%);
  }
  .screen--home { left: 233px; }
  .screen--mood { left: 510px; }
  .screen--graphs { left: 786px; }

  .status-bar {
    height: 12px; background: var(--bar-dark); color: #fff; font-size: 5.5px;
    display: flex; align-items: center; justify-content: space-between; padding: 0 5px;
  }
  .status-bar--light { background: var(--bar-light); color: #111; }

  .nav-row { position: absolute; top: 24px; left: 0; right: 0; height: 16px; display: flex; align-items: center; justify-content: space-between; padding: 0 20px 0 19px; }
  .nav-title { font-size: 8.5px; font-weight: 700; letter-spacing: 0.2px; }
  .nav-left { display: flex; align-items: center; gap: 8px; }
  .chev { font-size: 11px; font-weight: 300; line-height: 1; }

  /* home */
  .brand-mark { position: absolute; top: 57px; left: 74px; width: 38px; height: 38px; border-radius: 50%; background: #fff; opacity: 0.9; }
  .brand-name { position: absolute; top: 105px; width: 100%; text-align: center; font-size: 12.5px; font-weight: 400; letter-spacing: 0.3px; }
  .menu-list { position: absolute; top: 139px; left: 34px; width: 120px; display: flex; flex-direction: column; gap: 5px; }
  .menu-item { height: 18px; background: var(--btn); font-size: 10.5px; font-weight: 300; display: flex; align-items: center; justify-content: center; }
  .claim { position: absolute; top: 223px; left: 28px; right: 28px; text-align: center; font-size: 8px; line-height: 1.4; font-weight: 400; }
  .messages { position: absolute; top: 261px; left: 34px; width: 120px; height: 18px; background: var(--btn); font-size: 10.5px; font-weight: 400; display: flex; align-items: center; justify-content: center; }
  .sleep-now { position: absolute; top: 283px; left: 55px; width: 78px; height: 17px; background: var(--btn); font-size: 10px; font-weight: 400; display: flex; align-items: center; justify-content: center; }

  /* mood */
  .avatar { position: absolute; top: 44px; left: 81px; width: 26px; height: 30px; border: 1.5px solid #fff; background: linear-gradient(180deg, #c8a26e, #e6c4a2); }
  .question { position: absolute; top: 77px; width: 100%; text-align: center; font-size: 10.5px; font-weight: 300; }
  .mood-grid { position: absolute; top: 94px; left: 17px; display: grid; grid-template-columns: repeat(3, 44px); column-gap: 11px; row-gap: 13px; }
  .mood { width: 44px; height: 44px; border-radius: 6px; font-size: 8px; font-weight: 400; display: flex; align-items: center; justify-content: center; text-align: center; line-height: 1.1; }
  .mood--last { margin-top: -3px; }
  .sleep-time { position: absolute; top: 280px; left: 68px; display: flex; align-items: center; gap: 3px; font-size: 8px; font-weight: 700; }
  .sleep-time .label { margin-right: 5px; }
  .time-box { width: 15px; height: 14px; border-radius: 2px; border: 1px solid #cfe3f4; background: var(--time-box); font-size: 8px; font-weight: 400; display: flex; align-items: center; justify-content: center; }

  /* graphs */
  .chart-title { position: absolute; width: 100%; text-align: center; font-size: 6px; font-weight: 700; line-height: 1.15; }
  .chart { position: absolute; left: 18px; width: 152px; height: 108px; }
  .axis { position: absolute; left: 18px; width: 152px; display: flex; justify-content: space-between; font-size: 4.3px; text-align: center; line-height: 1.2; }
</style>
</head>
<body>

<section class="screen screen--home">
  <div class="status-bar"><span>●●●○○ NOVA</span><span>4:21 PM</span><span>100%</span></div>
  <div class="nav-row"><span class="chev">☰</span><span class="chev">&gt;</span></div>
  <div class="brand-mark"></div>
  <div class="brand-name">STEADY MIND</div>
  <nav class="menu-list">
    <div class="menu-item">Whats New Today?</div>
    <div class="menu-item">Tracking Graphs</div>
    <div class="menu-item">Personal Information</div>
  </nav>
  <p class="claim">According to our studies Steady<br>Mind App has potential to improve<br>your mood by 16%</p>
  <div class="messages">You have 03 messages</div>
  <div class="sleep-now">SLEEP NOW</div>
</section>

<section class="screen screen--mood">
  <div class="status-bar status-bar--light"><span>●●●○○ NOVA</span><span>4:21 PM</span><span>100%</span></div>
  <div class="nav-row"><span class="nav-left"><span class="chev">☰</span><span class="chev">&lt;</span></span><span class="nav-title">WHATS NEW TODAY</span><span class="chev">&gt;</span></div>
  <div class="avatar" role="img" aria-label="User profile photo"></div>
  <div class="question">How do you feel today ?</div>
  <div class="mood-grid">
    <div class="mood" style="background:var(--mood-1)">Insanely<br>Great</div>
    <div class="mood" style="background:var(--mood-2)">Great</div>
    <div class="mood" style="background:var(--mood-3)">Very<br>good</div>
    <div class="mood" style="background:var(--mood-4)">Good</div>
    <div class="mood" style="background:var(--mood-5)">Okay</div>
    <div class="mood" style="background:var(--mood-6)">So-so</div>
    <div class="mood" style="background:var(--mood-7)">Meh</div>
    <div class="mood" style="background:var(--mood-8)">Bad</div>
    <div class="mood" style="background:var(--mood-9)">Very bad</div>
    <div class="mood mood--last" style="background:var(--mood-10)">Couldn't<br>be worse</div>
  </div>
  <div class="sleep-time"><span class="label">Sleep Time</span><span class="time-box">08</span><span class="time-box">30</span><span class="time-box">30</span></div>
</section>

<section class="screen screen--graphs">
  <div class="status-bar"><span>●●●○○ NOVA</span><span>4:21 PM</span><span>100%</span></div>
  <div class="nav-row"><span class="nav-left"><span class="chev">☰</span><span class="chev">&lt;</span></span><span class="nav-title">TRACKING GRAPHS</span><span class="chev">&gt;</span></div>

  <div class="chart-title" style="top:46px">WEEK</div>
  <svg class="chart" style="top:55px" viewBox="0 0 152 108" aria-label="Weekly mood chart">
    <rect y="0" width="152" height="11" fill="#e8402a"/>
    <rect y="11" width="152" height="11" fill="#ee5a28"/>
    <rect y="22" width="152" height="11" fill="#ef782b"/>
    <rect y="33" width="152" height="11" fill="#e7962e"/>
    <rect y="44" width="152" height="11" fill="#d2a831"/>
    <rect y="55" width="152" height="11" fill="#a99a34"/>
    <rect y="66" width="152" height="11" fill="#8e9638"/>
    <rect y="77" width="152" height="11" fill="#7e8a3b"/>
    <rect y="88" width="152" height="10" fill="#707246"/>
    <rect y="98" width="152" height="10" fill="#66665a"/>
    <g stroke="rgba(255,255,255,0.25)" stroke-width="0.5">
      <line x1="12.7" y1="0" x2="12.7" y2="108"/><line x1="25.3" y1="0" x2="25.3" y2="108"/><line x1="38" y1="0" x2="38" y2="108"/><line x1="50.7" y1="0" x2="50.7" y2="108"/><line x1="63.3" y1="0" x2="63.3" y2="108"/><line x1="76" y1="0" x2="76" y2="108"/><line x1="88.7" y1="0" x2="88.7" y2="108"/><line x1="101.3" y1="0" x2="101.3" y2="108"/><line x1="114" y1="0" x2="114" y2="108"/><line x1="126.7" y1="0" x2="126.7" y2="108"/><line x1="139.3" y1="0" x2="139.3" y2="108"/>
    </g>
    <polyline fill="none" stroke="#fff" stroke-width="1" points="6,60 19,70 31,38 44,27 57,49 69,59 82,49 95,39 108,49 120,17 133,71 146,81"/>
    <g fill="#fff">
      <circle cx="6" cy="60" r="1.6"/><circle cx="19" cy="70" r="1.6"/><circle cx="31" cy="38" r="1.6"/><circle cx="44" cy="27" r="1.6"/><circle cx="57" cy="49" r="1.6"/><circle cx="69" cy="59" r="1.6"/><circle cx="82" cy="49" r="1.6"/><circle cx="95" cy="39" r="1.6"/><circle cx="108" cy="49" r="1.6"/><circle cx="120" cy="17" r="1.6"/><circle cx="133" cy="71" r="1.6"/><circle cx="146" cy="81" r="1.6"/>
    </g>
  </svg>
  <div class="axis" style="top:167px">
    <span>Mon<br>21/5</span><span>Tue<br>22/5</span><span>Wed<br>23/5</span><span>Thu<br>24/5</span><span>Fri<br>25/5</span><span>Sat<br>26/5</span><span>Sun<br>27/5</span><span>Mon<br>28/5</span><span>Tue<br>29/5</span><span>Wed<br>30/5</span><span>Thu<br>31/5</span><span>Fri<br>1/6</span>
  </div>

  <div class="chart-title" style="top:185px">MONTH<br>2015</div>
  <svg class="chart" style="top:200px" viewBox="0 0 152 108" aria-label="Monthly mood chart">
    <defs>
      <linearGradient id="month-fill" x1="0" y1="0" x2="0" y2="1">
        <stop offset="0" stop-color="#e8402a"/>
        <stop offset="0.3" stop-color="#ee7a2c"/>
        <stop offset="0.5" stop-color="#c9a632"/>
        <stop offset="0.7" stop-color="#8e9638"/>
        <stop offset="1" stop-color="#66665a"/>
      </linearGradient>
    </defs>
    <rect width="152" height="108" fill="url(#month-fill)"/>
    <g stroke="rgba(255,255,255,0.25)" stroke-width="0.5">
      <line x1="12.7" y1="0" x2="12.7" y2="108"/><line x1="25.3" y1="0" x2="25.3" y2="108"/><line x1="38" y1="0" x2="38" y2="108"/><line x1="50.7" y1="0" x2="50.7" y2="108"/><line x1="63.3" y1="0" x2="63.3" y2="108"/><line x1="76" y1="0" x2="76" y2="108"/><line x1="88.7" y1="0" x2="88.7" y2="108"/><line x1="101.3" y1="0" x2="101.3" y2="108"/><line x1="114" y1="0" x2="114" y2="108"/><line x1="126.7" y1="0" x2="126.7" y2="108"/><line x1="139.3" y1="0" x2="139.3" y2="108"/>
    </g>
    <line x1="0" y1="54" x2="152" y2="54" stroke="rgba(255,255,255,0.7)" stroke-width="0.6"/>
    <path fill="none" stroke="#fff" stroke-width="0.8" d="M0,54 C8,52 12,48 18,46 S26,44 30,42 S36,38 40,34 S46,40 50,38 S56,46 62,44 S70,40 76,42 S84,46 90,46 S96,44 100,50 S104,62 108,60 S112,46 116,40 S122,32 126,36 S130,46 134,42 S142,38 152,38"/>
  </svg>
  <div class="axis" style="top:314px">
    <span>Jan</span><span>Feb</span><span>Mar</span><span>Apr</span><span>May</span><span>Jun</span><span>Jul</span><span>Aug</span><span>Sep</span><span>Oct</span><span>Nov</span><span>Dec</span>
  </div>
</section>

</body>
</html>
```